SOLVE Study flyer

I need help designing a flyer for a research study that will include brain imaging in adolescents. The info is in the attached document. The study is called the Sequoia Outlook Lantern Valley Echo (SOLVE) study. Ideally this would be returned as a document that I can edit in the future as we will have several new recruitment phases (different age groups, etc. I also would love to have a logo designed as part of this project, but I recognize that might be a separate design request.

```html
<!DOCTYPE html>
<html lang="en">
<head>
<meta charset="utf-8">
<title>SOLVE Study flyer</title>
<link rel="stylesheet" href="https://fonts.googleapis.com/css2?family=Montserrat:wght@400;500;600;700;800&family=Source+Sans+3:wght@400;500&display=swap">
<style>
  :root {
    --navy: #0f1f66;
    --navy-deep: #0b1a5c;
    --orange: #ef9a1c;
    --orange-bright: #f5a623;
    --cream: #fdf1e2;
    --white: #ffffff;
    --ink: #111111;
    --photo-dark: #0c1630;
    --photo-mid: #3a4a6a;
    --photo-warm: #c9722c;
  }
  * { box-sizing: border-box; margin: 0; padding: 0; }
  html, body { width: 848px; height: 1200px; overflow: hidden; background: var(--white); }
  .flyer {
    position: relative; width: 848px; height: 1200px; overflow: hidden;
    background: linear-gradient(90deg, #ffffff 0%, #ffffff 30%, var(--cream) 55%, #ffffff 80%);
    font-family: "Source Sans 3", Arial, sans-serif; color: var(--ink);
  }

  .hero-image { position: absolute; left: 424px; top: 0; width: 424px; height: 517px; }

  .study-name {
    position: absolute; left: 0; top: 18px; width: 454px; text-align: center;
    font-family: "Montserrat", Arial, sans-serif; font-weight: 800; font-size: 68px;
    letter-spacing: 1px; color: var(--navy-deep); line-height: 1;
  }
  .study-full {
    position: absolute; left: 0; top: 88px; width: 454px; text-align: center;
    font-family: "Montserrat", Arial, sans-serif; font-weight: 700; font-size: 25px;
    line-height: 34px; color: var(--navy-deep);
  }
  .title-rule { position: absolute; left: 68px; top: 174px; width: 317px; height: 3px; background: var(--orange); }

  .hook {
    position: absolute; left: 20px; top: 196px;
    font-family: "Montserrat", Arial, sans-serif; font-weight: 700; font-size: 35px;
    line-height: 42px; color: var(--navy-deep);
  }
  .hook .accent { color: var(--orange-bright); }
  .hook-sub {
    position: absolute; left: 20px; top: 287px;
    font-family: "Montserrat", Arial, sans-serif; font-weight: 400; font-size: 28px;
    line-height: 34px; color: var(--navy-deep);
  }
  .intro {
    position: absolute; left: 21px; top: 372px; width: 430px;
    font-size: 20px; line-height: 28.6px; color: var(--ink);
  }

  .participation-band {
    position: absolute; left: 0; top: 517px; width: 848px; height: 437px;
    background: var(--navy); border-radius: 68px 0 100px 0;
  }
  .participation-title {
    position: absolute; left: 22px; top: 563px;
    font-family: "Montserrat", Arial, sans-serif; font-weight: 700; font-size: 29px;
    color: var(--white); line-height: 34px;
  }
  .participation-title .accent { color: var(--orange-bright); }

  .compensation { position: absolute; left: 491px; top: 547px; width: 357px; height: 65px; }
  .compensation svg { position: absolute; inset: 0; }
  .compensation-text {
    position: absolute; left: 38px; top: 0; height: 65px; display: flex; align-items: center; gap: 16px;
    font-family: "Montserrat", Arial, sans-serif; color: var(--navy-deep);
  }
  .compensation-text .label { font-size: 18px; font-weight: 500; }
  .compensation-text .amount { font-size: 29px; font-weight: 800; }

  .step { position: absolute; top: 640px; text-align: center; color: var(--white); font-size: 21px; line-height: 28.6px; }
  .step svg { display: block; margin: 0 auto 8px; }
  .step-questionnaires { left: 40px; width: 220px; }
  .step-interview { left: 300px; width: 250px; }
  .step-visit { left: 568px; width: 262px; }

  .eligibility-circle {
    position: absolute; left: -95px; top: 856px; width: 482px; height: 482px;
    border-radius: 50%; background: var(--orange);
  }
  .eligibility-title {
    position: absolute; left: 23px; top: 912px;
    font-family: "Montserrat", Arial, sans-serif; font-weight: 400; font-size: 31px;
    line-height: 36px; color: var(--navy-deep);
  }
  .eligibility-title strong { font-weight: 700; }
  .eligibility-list { position: absolute; left: 23px; top: 1004px; width: 300px; list-style: none; font-size: 20px; line-height: 28.6px; color: var(--navy-deep); }
  .eligibility-list li { position: relative; padding-left: 24px; }
  .eligibility-list li::before {
    content: ""; position: absolute; left: 1px; top: 9px; width: 14px; height: 11px;
    border-radius: 7px 7px 6px 6px; background: var(--navy-deep);
  }

  .contact { position: absolute; left: 440px; top: 1010px; color: var(--navy-deep); font-family: "Montserrat", Arial, sans-serif; }
  .contact .lead { font-size: 27px; line-height: 32px; font-weight: 400; }
  .contact .lead strong { font-weight: 700; }
  .contact .more { font-size: 21px; line-height: 27px; }
  .contact .call { font-size: 21px; line-height: 27px; font-weight: 800; color: var(--orange-bright); }
  .contact-email { position: absolute; left: 441px; top: 1108px; display: flex; align-items: center; gap: 16px; font-family: "Montserrat", Arial, sans-serif; font-size: 27px; color: var(--ink); }

  .print-code { position: absolute; right: 11px; bottom: 3px; font-family: Arial, sans-serif; font-size: 10px; color: var(--ink); }
</style>
</head>
<body>
<main class="flyer">
  <svg class="hero-image" role="img" aria-label="Photo: thoughtful teen girl in an orange sweater beside a glowing brain network graphic on a dark background" viewBox="0 0 424 517">
    <defs>
      <linearGradient id="heroTone" x1="0" y1="0" x2="0" y2="1">
        <stop offset="0" stop-color="var(--photo-dark)"/>
        <stop offset="0.55" stop-color="var(--photo-mid)"/>
        <stop offset="1" stop-color="var(--photo-warm)"/>
      </linearGradient>
    </defs>
    <path d="M150 0 C60 60 26 170 28 260 C30 380 20 460 0 517 L424 517 L424 0 Z" fill="url(#heroTone)"/>
  </svg>

  <h1 class="study-name">SOLVE</h1>
  <p class="study-full">Sequoia Outlook Lantern<br>Valley Echo Study</p>
  <div class="title-rule"></div>

  <h2 class="hook">Are you the parent of<br>a child age <span class="accent">10-17?</span></h2>
  <p class="hook-sub">Do they worry or overthink<br>negative emotions?</p>
  <p class="intro">Lantern Valley University researchers are seeking girls age 10-17 for a study about brain activity in emotions and decision-making and how they relate to puberty, anxiety and depression.</p>

  <section class="participation-band"></section>
  <h2 class="participation-title">Study participation <span class="accent">involves</span></h2>

  <div class="compensation">
    <svg viewBox="0 0 357 65" preserveAspectRatio="none"><path d="M0 0 H357 V65 H0 L20 32.5 Z" fill="var(--orange-bright)"/></svg>
    <div class="compensation-text"><span class="label">Compensation up to</span><span class="amount">$140</span></div>
  </div>

  <div class="step step-questionnaires">
    <svg width="76" height="72" viewBox="0 0 76 72" fill="none" stroke="#fff" stroke-width="3" stroke-linejoin="round">
      <path d="M64 10 h6 a4 4 0 0 1 4 4 v38 a4 4 0 0 1 -4 4 h-18 l-8 8 l-2 -8"/>
      <path d="M6 2 h52 a4 4 0 0 1 4 4 v40 a4 4 0 0 1 -4 4 h-36 l-10 9 v-9 h-6 a4 4 0 0 1 -4 -4 v-40 a4 4 0 0 1 4 -4 z"/>
      <path d="M26 18 a6 6 0 1 1 8 6 c-2 1 -3 3 -3 6" stroke-linecap="round"/>
      <circle cx="31" cy="37" r="1.5" fill="#fff" stroke="none"/>
    </svg>
    Online questionnaires<br>(parent and child)
  </div>

  <div class="step step-interview">
    <svg width="68" height="72" viewBox="0 0 68 68" fill="none" stroke="#fff" stroke-width="3" stroke-linecap="round">
      <path d="M34 4 A30 30 0 0 0 34 64"/>
      <path d="M34 4 A30 30 0 0 1 56 13"/>
      <path d="M50 7 l7 6 l-8 3"/>
      <path d="M62 26 A30 30 0 0 1 40 63" stroke-dasharray="4 6"/>
      <text x="34" y="43" text-anchor="middle" font-family="Montserrat, Arial, sans-serif" font-size="26" font-weight="500" fill="#fff" stroke="none">1h</text>
    </svg>
    One one-hour interview (online or in-person) where your child will discuss their thoughts
  </div>

  <div class="step step-visit">
    <svg width="70" height="72" viewBox="0 0 70 68" fill="none" stroke="#fff" stroke-width="3" stroke-linejoin="round">
      <path d="M35 52 C22 38 14 29 14 20 A21 21 0 0 1 56 20 C56 29 48 38 35 52 Z"/>
      <circle cx="35" cy="20" r="8"/>
      <path d="M22 50 C8 52 2 56 2 59 C2 63 17 66 35 66 C53 66 68 63 68 59 C68 56 62 52 48 50"/>
    </svg>
    One two-hour visit where your child will complete an MRI scan, answer questions about their puberty stage, and have a small hair sample taken to study puberty hormones
  </div>

  <div class="eligibility-circle"></div>
  <h2 class="eligibility-title">Your child may<br>be <strong>eligible</strong> if they</h2>
  <ul class="eligibility-list">
    <li>Are age 10-17</li>
    <li>Tend to worry or overthink negative thoughts</li>
    <li>Have not been diagnosed with psychosis, learning problems, or autism</li>
  </ul>

  <div class="contact">
    <p class="lead">Interested in <strong>participating?</strong></p>
    <p class="more">Want more information?</p>
    <p class="call">Please contact us!</p>
  </div>
  <div class="contact-email">
    <svg width="33" height="24" viewBox="0 0 33 24"><rect x="0" y="0" width="33" height="24" fill="var(--orange-bright)"/><path d="M1 1 L16.5 14 L32 1 M1 23 L12 11 M32 23 L21 11" stroke="#fff" stroke-width="2" fill="none"/></svg>
    <span>solvestudy@lvhealth.edu</span>
  </div>

  <span class="print-code">C50</span>
</main>
</body>
</html>
```